Online Dating Website called WinkAtWheel.com

PLEASE CAN ALL PARTICIPATING DESIGNERS PLEASE SUBMIT ALL PAGES AS DETAILED IN THE ORIGINAL BRIEF BELOW WITHIN 48 HOURS TO AVOID WINKATWHEEL EXTENDING THE CONTEST FURTHER.

We have an online dating website that is 95% fully functional and now require an exciting and creative designer to help us create the best dating experience. We are looking for your ideas on a couple of our key pages. These are our landing, profile and search page. We already have a homepage that we are happy with and winning designers will look to build upon the foundations of the homepage and extend them through their designs.

The premise of the site is the idea that if you've ever seen someone out driving and wished you could communicate because you found them attractive, how would you? Well with WinkAtWheel.com you can. Just enter their vehicle registration number (license plate) in to the website in order to get in touch, flirt and develop a relationship. It also allows users to find each other based on other criteria. It acts as both a specialist service and a normal dating website.

The pages that require developing are 1) our landing page, this is the page users see when they first login to the site, it comprises various pieces of information but it's primary function is a live feed of events generated based on the users favourited profiles and interactions with the user. 2) The profile page is the page where users can edit their own information, given the nature of this page we are looking for a creative design that gives this page some flair. 3) Finally we are looking for ideas for our search page, this page needs to provide a list of users who meet the user's search requirements and display the profile of a selected user.
Updates

Project Deadline Extended
Reason: We've asked for certain pages in our brief to be designed and this still hasn't been done. We've contacted the designers that have currently submitted designs and requested this several times. We still await for this to happen.

Target Market(s)

Male or Female age 18+

Industry/Entity Type

Dating

Requirements
Must have
• Our must have feature is a designer with an open mind. The functionality of the site must be present, all we ask is for you to be creative with the layout. Think out side of the box, change the colours, the layout, and the background as you feel. Make it look current and appealing to the user.
Nice to have
• Theme's carried through from the home page
Should not have
• Do not include Comic Sans or Times New Roman font in your designs.

```html
<!DOCTYPE html>
<html lang="en">
<head>
<meta charset="utf-8">
<title>WinkAtWheel.com – Feed</title>
<link href="https://fonts.googleapis.com/css2?family=Source+Sans+3:wght@400;600&display=swap" rel="stylesheet">
<style>
:root{
  --pink:#e4509a;
  --pink-dark:#d23d87;
  --pink-light:#ef7cb4;
  --sky:#5fb0f2;
  --sky-deep:#3f95e3;
  --ink:#2b2b2b;
  --navy:#1d3f6e;
  --panel:#ffffff;
  --card:#f6f9fc;
  --grey:#8a8a8a;
  --green:#58c03a;
  --bar:#000000;
  --foot:#3b3b3d;
}
*{box-sizing:border-box;margin:0;padding:0}
html,body{width:759px;height:1200px;overflow:hidden}
body{font-family:"Source Sans 3",sans-serif;color:var(--ink);background:linear-gradient(180deg,#62b4f4 0%,#4ea6ee 100%);position:relative}
.topbar{position:absolute;left:0;top:0;width:759px;height:50px;background:var(--bar);color:#fff;font-size:10px}
.brand{position:absolute;left:18px;top:17px;display:flex;align-items:center;gap:4px;font-size:10px;font-weight:600;color:#fff;white-space:nowrap}
.brand i{width:13px;height:13px;border-radius:50%;background:var(--pink);display:block}
.nav{position:absolute;top:18px;display:flex;gap:6px}
.nav.main{left:103px}.nav.side{right:23px}
.nav span.sep{color:#aaa}
.panel{position:absolute;background:var(--panel);border-radius:2px;box-shadow:0 1px 3px rgba(0,0,0,.15)}
.panel-head{height:24px;background:linear-gradient(180deg,var(--pink-light),var(--pink));color:#fff;font-size:12.5px;padding:3px 0 0 15px;position:relative}
.panel-head .toggle{position:absolute;right:8px;top:8px;width:8px;height:8px;background:#fff;border-radius:1px}
.panel-head .toggle::after{content:"";position:absolute;left:2px;top:3px;border:2px solid transparent;border-top:3px solid var(--pink)}
.photo{display:block;border:2px solid #fff;box-shadow:0 0 2px rgba(0,0,0,.3)}
.field{border:1px solid #ccc;border-radius:2px;height:19px;font-size:7px;color:var(--grey);padding:5px 8px;background:#fff;box-shadow:inset 0 1px 2px rgba(0,0,0,.1)}
.btn{display:inline-block;border-radius:2px;color:#fff;font-size:8.5px;text-align:center}
.btn.blue{background:linear-gradient(180deg,#6bbcf6,#3e97e4)}
.btn.pink{background:linear-gradient(180deg,var(--pink-light),var(--pink))}
.btn.dark{background:#111}
.searchrow{display:flex;height:20px}
.searchrow .field{flex:1;height:20px;border-right:none}
.searchbtn{width:21px;height:20px;background:#111;position:relative}
.searchbtn svg{position:absolute;left:5px;top:4px}
.profile{left:18px;top:66px;width:127px;height:232px}
.profile .photo{margin:8px auto 0;width:111px;height:112px;background:linear-gradient(160deg,#d9bd84,#6aa36b 70%,#3d8a4c)}
.profile .meta{font-size:8.5px;margin:5px 0 0 9px}
.status{display:flex;margin:7px 0 0 6px;width:114px;height:23px}
.status .field{flex:1;height:23px;padding-top:7px}
.status .btn{width:46px;height:23px;line-height:23px}
.profile .actions{display:flex;justify-content:space-between;margin:9px 9px 0 10px}
.profile .actions .btn{width:50px;height:17px;line-height:17px}
.seen{left:18px;top:310px;width:127px;height:138px}
.seen .body{padding:8px 6px 0}
.select{position:relative;margin-top:7px;font-style:italic}
.select::after{content:"";position:absolute;right:8px;top:7px;width:3px;height:3px;border-right:1px solid #444;border-bottom:1px solid #444;transform:rotate(45deg)}
.seen .btn{float:right;margin-top:9px;width:50px;height:17px;line-height:17px}
.stats{left:18px;top:462px;width:127px;height:212px;font-size:8px}
.list{padding:6px 0 0 7px}
.list .group{font-size:9.5px;margin:2px 0 5px}
.list .row{display:flex;justify-content:space-between;width:100px;line-height:13.5px}
.list .gap{height:8px}
.filter{left:18px;top:685px;width:127px;height:165px;font-size:8px}
.tick{display:inline-block;width:10px;height:8px}
.favs{left:18px;top:862px;width:127px;height:274px}
.favs .body{padding:8px 7px 0 7px}
.fav{display:flex;gap:6px;margin-top:12px;font-size:7px;line-height:8.5px;height:33px}
.fav .photo{width:32px;height:32px;flex:none}
.card{position:absolute;left:160px;width:442px;height:101px;background:var(--card);border-radius:3px;box-shadow:0 1px 3px rgba(0,0,0,.15)}
.card h2{position:absolute;left:14px;top:8px;font-size:12.5px;font-weight:400;color:var(--navy)}
.card .photo{position:absolute;left:14px;top:29px;width:86px;height:61px}
.card p{position:absolute;left:116px;top:40px;width:250px;font-size:7.2px;line-height:10px;color:#444}
.card .more{position:absolute;left:307px;top:80px;font-size:6.6px;color:#c0392b;display:flex;align-items:center;gap:4px}
.card .more i{width:7px;height:6px;border:1px solid #e7b04a;display:block}
.card .tab{position:absolute;left:387px;top:6px;width:55px;height:82px;background:var(--pink);color:#fff;font-size:8px;padding:19px 0 0 11px;line-height:13px}
.card .like{display:flex;align-items:center;gap:6px;margin-top:6px}
.welcome{position:absolute;left:618px;top:66px;width:127px;height:137px;background:linear-gradient(180deg,var(--sky-deep),#2f86d6);border-radius:2px;color:#fff;font-size:14.5px;line-height:19px;padding:22px 18px 0 22px;box-shadow:0 1px 3px rgba(0,0,0,.2)}
.matches{left:618px;top:218px;width:127px;height:314px}
.news{padding:6px 0 0 5px;font-size:7px}
.news div{display:flex;align-items:center;gap:5px;line-height:14.6px}
.news b{width:7px;height:6px;background:var(--pink);border-radius:1px;display:block}
.user{display:flex;align-items:center;gap:8px;margin:0 8px 0 8px;height:50px;border-bottom:1px solid #eee;font-size:7.5px}
.user:last-child{border-bottom:none}
.user .photo{width:31px;height:31px}
.users{margin-top:5px}
.bgselect{left:618px;top:549px;width:127px;height:314px}
.swatches{display:grid;grid-template-columns:48px 48px;column-gap:10px;row-gap:15px;padding:12px 0 0 8px}
.swatches span{height:42px;border:1px solid #ddd;display:block}
.footer{position:absolute;left:0;top:1126px;width:759px;height:74px;background:var(--foot);color:#ddd;font-size:7px;z-index:1}
.chat{position:absolute;left:668px;top:1110px;width:91px;height:40px;background:#2f2f31;border-radius:4px 0 0 0;color:#fff;font-size:8.5px;display:flex;align-items:center;gap:6px;padding-left:11px;z-index:2;white-space:nowrap}
.chat i{width:22px;height:18px;border-radius:50%;background:#47b6f0;display:block;flex:none}
.social{position:absolute;left:32px;top:42px;display:flex;gap:8px}
.social span{width:16px;height:16px;border-radius:2px;display:block}
.copy{position:absolute;right:12px;top:38px;text-align:right;line-height:13px}
</style>
</head>
<body>
<header class="topbar">
  <div class="brand"><i></i>WinkAtWheel</div>
  <nav class="nav main"><span>Home</span><span class="sep">|</span><span>Profile</span><span class="sep">|</span><span>Messages</span><span class="sep">|</span><span>Matches</span><span class="sep">|</span><span>Search</span></nav>
  <nav class="nav side"><span>Support</span><span class="sep">|</span><span>My Account</span></nav>
</header>

<section class="panel profile">
  <div class="panel-head">Rosy</div>
  <div class="photo" role="img" aria-label="Profile photo of the member"></div>
  <div class="meta">23 years old - Castleford</div>
  <div class="status"><div class="field">How are You?</div><span class="btn dark">Update</span></div>
  <div class="actions"><span class="btn blue">Profile</span><span class="btn pink">Upload</span></div>
</section>

<section class="panel seen">
  <div class="panel-head">Seen Someone?</div>
  <div class="body">
    <div class="searchrow"><div class="field">Search</div><div class="searchbtn"><svg width="11" height="11" viewBox="0 0 11 11"><circle cx="4" cy="4" r="3" fill="none" stroke="#fff" stroke-width="1.5"/><line x1="6" y1="6" x2="10" y2="10" stroke="#fff" stroke-width="2"/></svg></div></div>
    <div class="field select">Make</div>
    <div class="field select">Colour</div>
    <span class="btn blue">Search</span>
  </div>
</section>

<section class="panel stats">
  <div class="panel-head">Your Stats<span class="toggle"></span></div>
  <div class="list">
    <div class="group">Likes 24</div>
    <div class="row"><span>Images you have liked</span><span>32</span></div>
    <div class="row"><span>Images you have liked</span><span>32</span></div>
    <div class="row"><span>Images you have liked</span><span>32</span></div>
    <div class="gap"></div>
    <div class="group">Messages &nbsp;171</div>
    <div class="row"><span>Images you have liked</span><span>32</span></div>
    <div class="row"><span>Images you have liked</span><span>32</span></div>
    <div class="gap"></div>
    <div class="group">Favourites &nbsp;20</div>
    <div class="row"><span>Images you have liked</span><span>12</span></div>
    <div class="row"><span>Images you have liked</span><span>8</span></div>
  </div>
</section>

<section class="panel filter">
  <div class="panel-head">Feed Filter<span class="toggle"></span></div>
  <div class="list">
    <div class="group">Status Updates</div>
    <div class="row"><span>Status by others</span><svg class="tick" viewBox="0 0 10 8"><path d="M1 4l3 3 5-6" fill="none" stroke="#58c03a" stroke-width="2"/></svg></div>
    <div class="row"><span>Status by others</span><svg class="tick" viewBox="0 0 10 8"><path d="M1 4l3 3 5-6" fill="none" stroke="#58c03a" stroke-width="2"/></svg></div>
    <div class="row"><span>Status by others</span><svg class="tick" viewBox="0 0 10 8"><path d="M1 4l3 3 5-6" fill="none" stroke="#58c03a" stroke-width="2"/></svg></div>
    <div class="gap"></div>
    <div class="group">Profile Updates</div>
    <div class="row"><span>Status by others</span><svg class="tick" viewBox="0 0 10 8"><path d="M1 4l3 3 5-6" fill="none" stroke="#58c03a" stroke-width="2"/></svg></div>
    <div class="row"><span>Status by others</span><svg class="tick" viewBox="0 0 10 8"><path d="M1 4l3 3 5-6" fill="none" stroke="#58c03a" stroke-width="2"/></svg></div>
    <div class="row"><span>Status by others</span><svg class="tick" viewBox="0 0 10 8"><path d="M1 4l3 3 5-6" fill="none" stroke="#58c03a" stroke-width="2"/></svg></div>
  </div>
</section>

<section class="panel favs">
  <div class="panel-head">Your Favourites</div>
  <div class="body">
    <div class="searchrow"><div class="field">Type a name</div><div class="searchbtn"><svg width="11" height="11" viewBox="0 0 11 11"><circle cx="4" cy="4" r="3" fill="none" stroke="#fff" stroke-width="1.5"/><line x1="6" y1="6" x2="10" y2="10" stroke="#fff" stroke-width="2"/></svg></div></div>
    <div class="fav"><span class="photo" role="img" aria-label="Favourite member photo" style="background:#6b5a4a"></span><div><br>David<br>22 years old<br>Leeds</div></div>
    <div class="fav"><span class="photo" role="img" aria-label="Favourite member photo" style="background:#5a2c3a"></span><div><br>Rosy<br>24 years old</div></div>
    <div class="fav"><span class="photo" role="img" aria-label="Favourite member photo" style="background:#6b5a4a"></span><div><br>David<br>22 years old<br>Leeds</div></div>
    <div class="fav"><span class="photo" role="img" aria-label="Favourite member photo" style="background:#5a2c3a"></span><div><br>Rosy<br>24 years old</div></div>
  </div>
</section>

<main>
  <article class="card" style="top:70px"><h2>Loreum Ipsum dollar Amet</h2><span class="photo" role="img" aria-label="Member photo" style="background:linear-gradient(135deg,#ddd,#5b4a44)"></span><p>E-Commerce is a major progress in technology that has changed the way in which the customers now purchase , products and the services.E-Commerce is a major E-Commerce is a major progress in technology that has changed the way</p><span class="more">READ MORE <i></i></span><div class="tab">Tuesday<br>22:56<div class="like"><svg width="11" height="10" viewBox="0 0 12 11"><path d="M6 10.5L1 5.5A3 3 0 016 1.6 3 3 0 0111 5.5z" fill="#fff"/></svg>Like</div></div></article>
  <article class="card" style="top:191px"><h2>Loreum Ipsum dollar Amet</h2><span class="photo" role="img" aria-label="Couple photo" style="background:linear-gradient(135deg,#b08a6a,#4a3a30)"></span><p>E-Commerce is a major progress in technology that has changed the way in which the customers now purchase , products and the services.E-Commerce is a major E-Commerce is a major progress in technology that has changed the way</p><span class="more">READ MORE <i></i></span><div class="tab">Tuesday<br>22:56<div class="like"><svg width="11" height="10" viewBox="0 0 12 11"><path d="M6 10.5L1 5.5A3 3 0 016 1.6 3 3 0 0111 5.5z" fill="#fff"/></svg>Like</div></div></article>
  <article class="card" style="top:311px"><h2>Loreum Ipsum dollar Amet</h2><span class="photo" role="img" aria-label="Member photo" style="background:linear-gradient(135deg,#7a4a2a,#d4a88a)"></span><p>E-Commerce is a major progress in technology that has changed the way in which the customers now purchase , products and the services.E-Commerce is a major E-Commerce is a major progress in technology that has changed the way</p><span class="more">READ MORE <i></i></span><div class="tab">Tuesday<br>22:56<div class="like"><svg width="11" height="10" viewBox="0 0 12 11"><path d="M6 10.5L1 5.5A3 3 0 016 1.6 3 3 0 0111 5.5z" fill="#fff"/></svg>Like</div></div></article>
  <article class="card" style="top:432px"><h2>Loreum Ipsum dollar Amet</h2><span class="photo" role="img" aria-label="Member photo" style="background:linear-gradient(135deg,#2a1a14,#c08a6c)"></span><p>E-Commerce is a major progress in technology that has changed the way in which the customers now purchase , products and the services.E-Commerce is a major E-Commerce is a major progress in technology that has changed the way</p><span class="more">READ MORE <i></i></span><div class="tab">Tuesday<br>22:56<div class="like"><svg width="11" height="10" viewBox="0 0 12 11"><path d="M6 10.5L1 5.5A3 3 0 016 1.6 3 3 0 0111 5.5z" fill="#fff"/></svg>Like</div></div></article>
  <article class="card" style="top:552px"><h2>Loreum Ipsum dollar Amet</h2><span class="photo" role="img" aria-label="Member photo" style="background:linear-gradient(135deg,#2b3c6a,#c8957a)"></span><p>E-Commerce is a major progress in technology that has changed the way in which the customers now purchase , products and the services.E-Commerce is a major E-Commerce is a major progress in technology that has changed the way</p><span class="more">READ MORE <i></i></span><div class="tab">Tuesday<br>22:56<div class="like"><svg width="11" height="10" viewBox="0 0 12 11"><path d="M6 10.5L1 5.5A3 3 0 016 1.6 3 3 0 0111 5.5z" fill="#fff"/></svg>Like</div></div></article>
  <article class="card" style="top:673px"><h2>Loreum Ipsum dollar Amet</h2><span class="photo" role="img" aria-label="Two friends photo" style="background:linear-gradient(135deg,#e8d7a0,#6a4a3a)"></span><p>E-Commerce is a major progress in technology that has changed the way in which the customers now purchase , products and the services.E-Commerce is a major E-Commerce is a major progress in technology that has changed the way</p><span class="more">READ MORE <i></i></span><div class="tab">Tuesday<br>22:56<div class="like"><svg width="11" height="10" viewBox="0 0 12 11"><path d="M6 10.5L1 5.5A3 3 0 016 1.6 3 3 0 0111 5.5z" fill="#fff"/></svg>Like</div></div></article>
  <article class="card" style="top:793px"><h2>Loreum Ipsum dollar Amet</h2><span class="photo" role="img" aria-label="Member photo" style="background:linear-gradient(135deg,#a8c8e8,#1e1e22)"></span><p>E-Commerce is a major progress in technology that has changed the way in which the customers now purchase , products and the services.E-Commerce is a major E-Commerce is a major progress in technology that has changed the way</p><span class="more">READ MORE <i></i></span><div class="tab">Tuesday<br>22:56<div class="like"><svg width="11" height="10" viewBox="0 0 12 11"><path d="M6 10.5L1 5.5A3 3 0 016 1.6 3 3 0 0111 5.5z" fill="#fff"/></svg>Like</div></div></article>
  <article class="card" style="top:914px"><h2>Loreum Ipsum dollar Amet</h2><span class="photo" role="img" aria-label="Member photo" style="background:linear-gradient(135deg,#f2f2f2,#3a3a40)"></span><p>E-Commerce is a major progress in technology that has changed the way in which the customers now purchase , products and the services.E-Commerce is a major E-Commerce is a major progress in technology that has changed the way</p><span class="more">READ MORE <i></i></span><div class="tab">Tuesday<br>22:56<div class="like"><svg width="11" height="10" viewBox="0 0 12 11"><path d="M6 10.5L1 5.5A3 3 0 016 1.6 3 3 0 0111 5.5z" fill="#fff"/></svg>Like</div></div></article>
  <article class="card" style="top:1035px"><h2>Loreum Ipsum dollar Amet</h2><span class="photo" role="img" aria-label="Member photo" style="background:linear-gradient(135deg,#e4e8ec,#4a4e58)"></span><p>E-Commerce is a major progress in technology that has changed the way in which the customers now purchase , products and the services.E-Commerce is a major E-Commerce is a major progress in technology that has changed the way</p><span class="more">READ MORE <i></i></span><div class="tab">Tuesday<br>22:56<div class="like"><svg width="11" height="10" viewBox="0 0 12 11"><path d="M6 10.5L1 5.5A3 3 0 016 1.6 3 3 0 0111 5.5z" fill="#fff"/></svg>Like</div></div></article>
</main>

<aside class="welcome">Welcome to our site is cur-rently free during beta testing.</aside>

<section class="panel matches">
  <div class="panel-head">Your Matches</div>
  <div class="news">
    <div><b></b>WAW has uploded a new image</div>
    <div><b></b>WAW has uploded a new image</div>
    <div><b></b>WAW has uploded a new image</div>
    <div><b></b>WAW has uploded a new image</div>
    <div><b></b>WAW has uploded a new image</div>
    <div><b></b>WAW has uploded a new image</div>
  </div>
  <div class="users">
    <div class="user"><span class="photo" role="img" aria-label="Match photo" style="background:#5a4a3e"></span>User Name</div>
    <div class="user"><span class="photo" role="img" aria-label="Match photo" style="background:#5a6a4a"></span>User Name</div>
    <div class="user"><span class="photo" role="img" aria-label="Match photo" style="background:#8a98a8"></span>User Name</div>
    <div class="user"><span class="photo" role="img" aria-label="Match photo" style="background:#8a6a54"></span>User Name</div>
  </div>
</section>

<section class="panel bgselect">
  <div class="panel-head">Background Select</div>
  <div class="swatches">
    <span role="img" aria-label="Pink hearts background" style="background:linear-gradient(135deg,#f27ab8,#fbd0e6)"></span>
    <span role="img" aria-label="Parchment background" style="background:linear-gradient(135deg,#d8b888,#c9a070)"></span>
    <span role="img" aria-label="Blue waves background" style="background:linear-gradient(160deg,#0c2a5a,#3a88d8)"></span>
    <span role="img" aria-label="Colourful shapes background" style="background:linear-gradient(135deg,#222,#e83a5a 60%,#f6d23a)"></span>
    <span role="img" aria-label="Night city lights background" style="background:linear-gradient(180deg,#1a2a8a,#0a0a14)"></span>
    <span role="img" aria-label="Golden glow background" style="background:linear-gradient(135deg,#fbe36a,#f0a81a)"></span>
    <span role="img" aria-label="Lime background" style="background:linear-gradient(135deg,#c8e050,#98c030)"></span>
    <span role="img" aria-label="Green sparkle background" style="background:linear-gradient(135deg,#0a3a0a,#58b83a)"></span>
  </div>
</section>

<footer class="footer">
  <div class="social">
    <span style="background:#3b5a9a"></span><span style="background:#3aa8e0"></span><span style="background:#555"></span><span style="background:#f28a1a"></span><span style="background:#d62a2a"></span><span style="background:#8aa8c8"></span>
  </div>
  <div class="copy">© 2013 winkatwheel.comAll rights reserved<br>X2</div>
</footer>

<div class="chat"><i></i>Open Chat</div>
</body>
</html>
```